Graphic designs required for HR consulting Website

We need to items designed to be used on our website and in presentations.
Please view our website for design ideas.
http://www.brightmoor.com.au.42.vexaloft.pw
See attached Powerpoint doc for more info.
InfoGraphic 1
Needs to be turned into an infographic that will be embedded into the Brightmoor HR website.
The fonts should be Helvetica Neue and should have the look and feel of the website.
InfoGraphic 2
Needs to be turned into an infographic that will be embedded into the Brightmoor HR website and used in PPT and WORD proposals.
The fonts should be Helvetica Neue, the look and
feel should be consistent with the first infographic.
A mountain analogy is needed that shows how the sequence of services will come together to take businesses on the journey to becoming great.
2 versions of the same information are shown on the following slides. The first is for ease of visibility, the second is to show the sequence of services on the journey.
Samples of possible design ideas for inspiration are at bottom of ppt.
Consulting
- Helvetica

```html
<!DOCTYPE html>
<html lang="en">
<head>
<meta charset="utf-8">
<title>Brightmoor HR – Business needs and how we can help</title>
<link rel="stylesheet" href="https://fonts.googleapis.com/css2?family=Roboto:wght@300;400&display=swap">
<style>
  :root {
    --page: #f8f6f1;
    --navy: #042a47;
    --sky: #2a8fd0;
    --white: #ffffff;
    --heading-ink: #12355a;
    --shadow: rgba(60, 60, 60, 0.35);
  }
  * { margin: 0; padding: 0; box-sizing: border-box; }
  html, body { width: 1200px; height: 847px; overflow: hidden; background: var(--page); }
  .infographic {
    position: relative;
    width: 1200px;
    height: 847px;
    background: var(--page);
    font-family: "Roboto", "Helvetica Neue", Arial, sans-serif;
    font-weight: 300;
  }
  .infographic__bands { position: absolute; left: 0; top: 0; }
  .column-title {
    position: absolute;
    top: 41px;
    font-size: 33px;
    font-weight: 300;
    line-height: 40px;
    white-space: nowrap;
    transform: translateX(-50%);
  }
  .column-title--needs { left: 344px; color: var(--heading-ink); }
  .column-title--help { left: 877px; color: var(--sky); }

  .need, .service { position: absolute; color: var(--white); }
  .need__title, .service__title {
    font-size: 36px;
    line-height: 35px;
    letter-spacing: -0.6px;
    white-space: nowrap;
    text-transform: uppercase;
  }
  .need__text, .service__text {
    font-size: 18px;
    line-height: 23.6px;
    white-space: nowrap;
  }
  .need { left: 137px; }
  .service { left: 749px; }
  .service__text { line-height: 28px; }

  .need--compliance .need__text { margin-top: 7px; }
  .need--operations .need__text { margin-top: 15px; }
  .need--strategy .need__text { margin-top: 14px; }
  .service--on-demand .service__text { margin-top: 15px; }
  .service--manager .service__text { margin-top: 13px; }
  .service--expertise .service__text { margin-top: 13px; }
</style>
</head>
<body>
<main class="infographic">
  <svg class="infographic__bands" width="1200" height="847" viewBox="0 0 1500 1059" aria-hidden="true">
    <defs>
      <radialGradient id="band-shadow" cx="50%" cy="50%" r="50%">
        <stop offset="0%" stop-color="var(--shadow)"/>
        <stop offset="100%" stop-color="rgba(60,60,60,0)"/>
      </radialGradient>
      <g id="service-band">
        <rect x="600" y="0" width="1306" height="238" fill="var(--sky)"/>
        <polygon points="0,0 715,0 798,83 643,238 0,238" fill="var(--white)"/>
        <g fill="none" stroke="var(--sky)" stroke-width="2.5">
          <polyline points="697,0 780,83 625,238"/>
          <polyline points="703,0 786,83 631,238"/>
          <polyline points="709,0 792,83 637,238"/>
        </g>
        <polygon points="0,0 659,0 742,83 587,238 0,238" fill="var(--sky)"/>
        <polygon points="0,0 623,0 706,83 551,238 0,238" fill="var(--navy)"/>
      </g>
    </defs>
    <ellipse cx="755" cy="390" rx="500" ry="16" fill="url(#band-shadow)"/>
    <ellipse cx="755" cy="682" rx="500" ry="16" fill="url(#band-shadow)"/>
    <ellipse cx="755" cy="960" rx="500" ry="16" fill="url(#band-shadow)"/>
    <use href="#service-band" x="104" y="142" transform="translate(0 0)"/>
    <use href="#service-band" x="100" y="434"/>
    <use href="#service-band" x="99" y="712"/>
    <rect x="1407" y="142" width="100" height="238" fill="var(--page)"/>
    <rect x="1410" y="434" width="100" height="238" fill="var(--page)"/>
    <rect x="1411" y="712" width="100" height="238" fill="var(--page)"/>
  </svg>

  <h2 class="column-title column-title--needs">Business needs</h2>
  <h2 class="column-title column-title--help">How we can help you</h2>

  <section class="need need--compliance" style="top:137px">
    <h3 class="need__title">Compliance</h3>
    <p class="need__text">Trusted advice on people issues including<br>Fair Work Act compliance, redundancies,<br>performance management,<br>terminations, policies and safety.</p>
  </section>
  <section class="service service--on-demand" style="top:167px">
    <h3 class="service__title">HR On-Demand</h3>
    <p class="service__text">Monthly subscription</p>
  </section>

  <section class="need need--operations" style="top:375px">
    <h3 class="need__title">HR Operations</h3>
    <p class="need__text">Operational HR support including recruit-<br>ment, performance management and<br>training.</p>
  </section>
  <section class="service service--manager" style="top:372px">
    <h3 class="service__title">Onsite or remote<br>HR manager</h3>
    <p class="service__text">Outsourced HR (annual subscription)<br>OR adhoc HR support (fixed fee projects)</p>
  </section>

  <section class="need need--strategy" style="top:595px">
    <h3 class="need__title">People &amp; Performance<br>Strategy</h3>
    <p class="need__text">Business strategy and planning, strategic HR<br>frameworks and interventions to fuel your growth.</p>
  </section>
  <section class="service service--expertise" style="top:603px">
    <h3 class="service__title">Strategic<br>Expertise</h3>
    <p class="service__text">Fixed fee project based expertise</p>
  </section>
</main>
</body>
</html>
```